Design a website for a newly developed Delta 8 THC Company

Design a responsive Website with the following goals in mind:
- Built on Wordpress/WooCommerce theme. Please use this when designing for ease of integration.
- Build trust with website visitors with an engaging, informative content driven website, that leads to a conversion of product purchase and repeat business. We will also be driving consumers to businesses that carry our products as well.
- The website will embody a lifestyle feel and make the visitor identify with the content.
- The website will allow for super charged SEO and other digital marketing and advertising strategies and tactics used to increase discovery, awareness, and conversion.
Please see additional goals in the uploaded files.
Target Market(s)
Male/Female 21-
Industry/Entity Type
Cannabis/Hemp
Coding
Coded - Design and coding required
Number of Pages Required
5+ page
Font styles to use
Other font styles liked:
- Montserrat
Look and feel
Each slider illustrates characteristics of the customer's brand and the style your logo design should communicate.

```html
<!DOCTYPE html>
<html lang="en">
<head>
<meta charset="utf-8">
<title>Solven — Delta-8 Gummies</title>
<link href="https://fonts.googleapis.com/css2?family=Josefin+Sans:wght@300;400;600;700&family=Montserrat:wght@300;400;500;600;700&family=Libre+Baskerville&display=swap" rel="stylesheet">
<style>
:root{
  --ink:#1d1d1d;
  --navy:#33323f;
  --gold:#d6cd5c;
  --gold-text:#b9a227;
  --card-top:#ecebc6;
  --card-bottom:#f3f3f3;
  --cream:#fcfcf1;
  --mist:#f5f5f5;
  --muted:#8a8a95;
  --white:#ffffff;
}
*{margin:0;padding:0;box-sizing:border-box}
html,body{width:1200px;height:2880px;overflow:hidden}
body{position:relative;background:var(--white);font-family:"Montserrat",sans-serif;color:var(--ink)}
.abs{position:absolute}
.center{text-align:center}

/* header */
.brand-box{left:0;top:0;width:121px;height:121px;background:var(--navy);z-index:3;display:flex;flex-direction:column;align-items:center;justify-content:center;gap:10px}
.brand-dot{width:44px;height:44px;border-radius:50%;border:2px solid var(--gold-text)}
.brand-name{font-family:"Josefin Sans",sans-serif;font-weight:400;font-size:14px;letter-spacing:5px;color:var(--gold-text)}
.nav-bar{left:121px;top:34px;width:1079px;height:52px;background:rgba(255,255,255,.93);z-index:2}
.nav-link{top:52px;font-size:12px;color:#333;z-index:3;letter-spacing:.5px}
.nav-icon{top:52px;z-index:3}

/* hero */
.hero{left:0;top:0;width:1200px;height:562px;background:linear-gradient(180deg,#7a8a55 0%,#4f6a36 35%,#3d5a2e 60%,#2a3a22 100%)}
.hero-shade{left:0;top:300px;width:1200px;height:262px;background:linear-gradient(180deg,rgba(0,0,0,0),rgba(0,0,0,.35))}
.hero-title{left:0;top:376px;width:1200px;font-family:"Josefin Sans",sans-serif;font-weight:700;font-size:52px;color:var(--white)}
.hero-sub{left:0;top:436px;width:1200px;font-family:"Josefin Sans",sans-serif;font-weight:300;font-size:26px;letter-spacing:2px;color:var(--white)}
.btn-pill{left:535px;top:481px;width:130px;height:37px;border-radius:19px;background:var(--gold);font-size:10px;font-weight:700;display:flex;align-items:center;justify-content:center;color:#222}

/* products */
.section-title{left:0;width:1200px;font-family:"Josefin Sans",sans-serif;font-weight:600;font-size:23px;color:var(--ink)}
.card{top:678px;width:206px;height:286px;background:var(--card-bottom)}
.card-top{left:0;top:0;width:206px;height:137px;background:var(--card-top)}
.pouch{left:50px;top:10px;width:106px;height:178px;border-radius:10px 10px 14px 14px;background:linear-gradient(160deg,#2c2c2c,#0f0f0f)}
.card-name{left:0;top:212px;width:206px;font-size:11px;font-weight:500;line-height:14px}
.card-price{left:0;top:250px;width:206px;font-size:17px;font-weight:700}

/* stories */
.stories{left:0;top:1038px;width:681px;height:322px;background:var(--navy)}
.stories-title{left:0;top:1092px;width:786px;font-family:"Josefin Sans",sans-serif;font-weight:600;font-size:23px;color:var(--white)}
.stories-text{left:235px;top:1138px;width:316px;font-size:11.5px;font-weight:300;line-height:20px;color:#b6b5bf}
.read-more{left:363px;top:1286px;font-size:9px;font-weight:600;color:#6e6d7b;letter-spacing:.5px;border-bottom:1px solid #6e6d7b;padding-bottom:3px}
.stories-photo{left:681px;top:1038px;width:519px;height:322px;background:linear-gradient(150deg,#9cb37a 0%,#5f7a45 40%,#3b2a1e 70%,#a8846a 100%)}

/* features */
.features{left:0;top:1360px;width:1200px;height:156px;background:var(--cream)}
.feature{top:1394px;width:200px;text-align:center}
.feature svg{display:block;margin:0 auto 14px}
.feature p{font-size:10px;font-weight:500;line-height:17px;color:#333;letter-spacing:.3px}

/* testimonial */
.testimonial{left:0;top:1516px;width:1200px;height:385px;background:var(--mist)}
.ornament{left:559px;top:1580px}
.testi-title{left:0;top:1606px;width:1200px;font-family:"Josefin Sans",sans-serif;font-weight:700;font-size:46px;letter-spacing:3px;color:#222}
.avatar{left:573px;top:1679px;width:54px;height:54px;border-radius:50%;background:linear-gradient(180deg,#d9d5d0,#b9b0a6)}
.quote-mark{left:326px;top:1690px;font-family:"Libre Baskerville",serif;font-size:150px;color:#dcdcdc;line-height:1}
.testi-head{left:0;top:1748px;width:1200px;font-family:"Josefin Sans",sans-serif;font-weight:600;font-size:20px;color:#3b3b55}
.testi-text{left:0;top:1778px;width:1200px;font-size:13.5px;line-height:26px;color:#555;letter-spacing:.3px}
.testi-name{left:0;top:1834px;width:1200px;font-size:12px;color:var(--gold-text)}

/* subscribe */
.subscribe{left:0;top:1901px;width:1200px;height:273px;background:linear-gradient(100deg,#c9a23d 0%,#8a8a3a 30%,#4e6a34 55%,#2f4a26 100%)}
.sub-title{left:165px;top:1962px;font-family:"Josefin Sans",sans-serif;font-weight:700;font-size:46px;color:var(--white)}
.sub-text{left:165px;top:2015px;font-size:12px;color:var(--white)}
.email{left:162px;top:2048px;width:220px;height:37px;background:rgba(255,255,255,.9);display:flex;align-items:center;padding-left:14px;gap:10px;font-size:10px;color:#888}
.btn-go{left:382px;top:2048px;width:113px;height:37px;background:var(--gold);color:var(--white);font-size:9px;font-weight:700;letter-spacing:.5px;display:flex;align-items:center;justify-content:center}
.pack-big{left:828px;top:1974px;width:138px;height:244px;border-radius:14px;background:linear-gradient(160deg,#2e2e2e,#0c0c0c);box-shadow:0 24px 30px rgba(0,0,0,.25)}
.pack-small{left:966px;top:2008px;width:78px;height:196px;border-radius:10px;background:linear-gradient(160deg,#2a2a2a,#0c0c0c)}

/* instagram */
.insta-head{left:0;top:2246px;width:1200px;display:flex;align-items:center;justify-content:center;gap:14px}
.insta-head span{font-family:"Libre Baskerville",serif;font-size:38px;color:#222}
.insta-dot{width:14px;height:14px;border:2px solid var(--gold-text);border-radius:3px}
.tile{top:2317px;width:140px;height:140px}
.btn-follow{left:492px;top:2489px;width:216px;height:35px;background:var(--gold);color:var(--white);font-size:8.5px;font-weight:600;letter-spacing:1px;display:flex;align-items:center;justify-content:center}

/* footer */
.footer{left:0;top:2607px;width:1200px;height:273px;background:var(--navy)}
.foot-brand{left:188px;top:2680px;width:60px;display:flex;flex-direction:column;align-items:center;gap:8px}
.foot-brand .brand-dot{width:46px;height:46px}
.foot-brand .brand-name{font-size:11px;letter-spacing:4px}
.socials{left:187px;top:2761px;display:flex;gap:10px}
.socials i{display:block;width:7px;height:7px;border-radius:50%;background:#c8c7d0}
.foot-col{top:2680px;text-align:center;color:#c8c7d0}
.foot-col h4{font-family:"Josefin Sans",sans-serif;font-weight:600;font-size:13px;color:var(--white);margin-bottom:12px}
.foot-col li{list-style:none;font-size:10px;line-height:22px}
.phone{font-size:17px;color:var(--gold);margin-top:8px}
.foot-rule{left:98px;top:2837px;width:1004px;height:1px;background:#45445a}
.legal{top:2853px;font-size:9px;color:#7d7c8c}
</style>
</head>
<body>

<!-- hero -->
<div class="abs hero" role="img" aria-label="Woman in a straw hat holding a hemp leaf in a field of hemp plants"></div>
<div class="abs hero-shade"></div>
<div class="abs brand-box"><div class="brand-dot"></div><div class="brand-name">SOLVEN</div></div>
<div class="abs nav-bar"></div>
<span class="abs nav-link" style="left:603px">Home</span>
<span class="abs nav-link" style="left:708px">Shop</span>
<span class="abs nav-link" style="left:808px">Stories</span>
<span class="abs nav-link" style="left:919px">About</span>
<span class="abs nav-link" style="left:1025px">Blog</span>
<svg class="abs nav-icon" style="left:1119px;top:53px" width="12" height="14" viewBox="0 0 12 14" fill="none" stroke="#222" stroke-width="1.4"><rect x="1" y="4" width="10" height="9"/><path d="M4 4V2.5a2 2 0 0 1 4 0V4"/></svg>
<svg class="abs nav-icon" style="left:1156px;top:53px" width="14" height="14" viewBox="0 0 14 14" fill="none" stroke="#222" stroke-width="1.5"><circle cx="6" cy="6" r="4.5"/><path d="M9.5 9.5L13 13"/></svg>
<h1 class="abs hero-title center">100% Organic &amp; All Natural</h1>
<p class="abs hero-sub center">Shipping Out Today!!!</p>
<a class="abs btn-pill">BUY NOW</a>

<!-- products -->
<h2 class="abs section-title center" style="top:622px">Our Products</h2>
<div class="abs card" style="left:162px"><div class="abs card-top"></div><div class="abs pouch" role="img" aria-label="Black pouch of lemon delta-8 gummies"></div><p class="abs card-name center">Lemon<br>Gummies</p><p class="abs card-price center">$19.99</p></div>
<div class="abs card" style="left:386px"><div class="abs card-top"></div><div class="abs pouch" role="img" aria-label="Black pouch of sour apple delta-8 gummies"></div><p class="abs card-name center">Sour Apple<br>Gummies</p><p class="abs card-price center">$19.99</p></div>
<div class="abs card" style="left:609px"><div class="abs card-top"></div><div class="abs pouch" role="img" aria-label="Black pouch of blue raspberry delta-8 gummies"></div><p class="abs card-name center">Blue raspberry<br>Gummies</p><p class="abs card-price center">$19.99</p></div>
<div class="abs card" style="left:832px"><div class="abs card-top"></div><div class="abs pouch" role="img" aria-label="Black pouch of cherry delta-8 gummies"></div><p class="abs card-name center">Cherry<br>Gummies</p><p class="abs card-price center">$19.99</p></div>

<!-- stories -->
<div class="abs stories"></div>
<h2 class="abs stories-title center" style="width:786px">Our Stories</h2>
<p class="abs stories-text center">Ut wisi enim ad minim veniam, quis nostrud exerci tation ullamcorper suscipit lobortis nisl ut aliquip ex ea commodo consequat. Duis autem vel eum iriure dolor in hendrerit in vulputate velit esse molestie consequat, vel illum dolore eu feugiat nulla facilisis at vero eros et accumsan et iusto.</p>
<a class="abs read-more">READ MORE</a>
<div class="abs stories-photo" role="img" aria-label="Cupped hands holding soil with a young hemp seedling"></div>

<!-- features -->
<div class="abs features"></div>
<div class="abs feature" style="left:169px">
  <svg width="28" height="40" viewBox="0 0 28 40" fill="none" stroke="#2e3a55" stroke-width="1.5"><path d="M10 20v6L4 37h20l-6-11v-6"/><path d="M8 20h12"/><path d="M14 20V8M14 10c0-4 4-6 8-6 0 4-4 6-8 6zM14 13c0-3-3-5-6-5 0 3 3 5 6 5z"/><path d="M7 32h14"/></svg>
  <p>Crafted from<br>natural ingredients</p>
</div>
<div class="abs feature" style="left:389px">
  <svg width="30" height="40" viewBox="0 0 30 40" fill="none" stroke="#2e3a55" stroke-width="1.5"><path d="M14 8c-5 8-8 12-8 17a8 8 0 0 0 16 0c0-5-3-9-8-17z"/><path d="M25 5v6M22 8h6M4 30v4M2 32h4"/></svg>
  <p>Gluten and<br>Allergen Free</p>
</div>
<div class="abs feature" style="left:610px">
  <svg width="30" height="40" viewBox="0 0 30 40" fill="none" stroke="#2e3a55" stroke-width="1.5"><circle cx="15" cy="22" r="12"/><path d="M15 10a12 12 0 0 1 9 5"/></svg>
  <p>No Colorants<br>or Synthetic Fillers</p>
</div>
<div class="abs feature" style="left:838px">
  <svg width="30" height="40" viewBox="0 0 30 40" fill="none" stroke="#2e3a55" stroke-width="1.5"><path d="M15 9l10 4v8c0 7-5 11-10 13-5-2-10-6-10-13v-8z"/><path d="M10 21l4 4 6-7"/></svg>
  <p>100% safe &amp;<br>secure checkout</p>
</div>

<!-- testimonial -->
<div class="abs testimonial"></div>
<svg class="abs ornament" width="82" height="20" viewBox="0 0 82 20"><path d="M0 10h24M58 10h24" stroke="var(--gold)" stroke-width="1.2"/><circle cx="41" cy="10" r="8" fill="var(--gold)"/></svg>
<h2 class="abs testi-title center">Testimonial</h2>
<div class="abs avatar" role="img" aria-label="Portrait of the reviewer"></div>
<div class="abs quote-mark">&ldquo;</div>
<h3 class="abs testi-head center">Impressive!</h3>
<p class="abs testi-text center">Ut wisi enim ad minim veniam, quis nostrud exerci tation umcorper<br>suscipit lobortis nisl ut aliquip ex ea commodo conquat.</p>
<p class="abs testi-name center">- Velit Esse</p>

<!-- subscribe -->
<div class="abs subscribe" role="img" aria-label="Blurred warm background with a hemp leaf and a dripping oil drop"></div>
<h2 class="abs sub-title">Subscribe and Save</h2>
<p class="abs sub-text">Sed diam nonummy nibh euismod tincidunt ut looreet</p>
<div class="abs email"><svg width="12" height="9" viewBox="0 0 12 9" fill="none" stroke="#aaa"><rect x=".5" y=".5" width="11" height="8"/><path d="M.5.5l5.5 4 5.5-4"/></svg>Enter Email Address</div>
<a class="abs btn-go">GET STARTED</a>
<div class="abs pack-small" role="img" aria-label="Smaller black pouch of cherry gummies"></div>
<div class="abs pack-big" role="img" aria-label="Black pouch of blue raspberry gummies"></div>

<!-- instagram -->
<div class="abs insta-head"><i class="insta-dot"></i><span>@SOLVEN</span></div>
<div class="abs tile" style="left:162px;background:linear-gradient(150deg,#9bb580,#4a3a2c)" role="img" aria-label="Hands holding a hemp seedling in soil"></div>
<div class="abs tile" style="left:309px;background:linear-gradient(160deg,#e2e6dc,#8d8a7c)" role="img" aria-label="Smiling woman outdoors"></div>
<div class="abs tile" style="left:456px;background:radial-gradient(circle at 50% 45%,#c82a2a 0 35%,#e5d84a 60%,#9ec44a 100%)" role="img" aria-label="Heart shape made of red candies on yellow"></div>
<div class="abs tile" style="left:603px;background:linear-gradient(170deg,#f1c58d,#b87a54)" role="img" aria-label="Couple hugging at sunset"></div>
<div class="abs tile" style="left:750px;background:linear-gradient(160deg,#dfe8ee,#9fb4c4)" role="img" aria-label="Laughing couple outdoors"></div>
<div class="abs tile" style="left:897px;background:linear-gradient(160deg,#b48a5e,#6f4a2c)" role="img" aria-label="Bowl of colourful gummy bears on wood"></div>
<a class="abs btn-follow">FOLLOW US ON INSTAGRAM</a>

<!-- footer -->
<footer class="abs footer"></footer>
<div class="abs foot-brand"><div class="brand-dot"></div><div class="brand-name">SOLVEN</div></div>
<div class="abs socials"><i></i><i></i><i></i><i></i></div>
<div class="abs foot-col" style="left:326px;width:80px"><h4>Links</h4><ul><li>Home</li><li>Shop</li><li>Stories</li><li>About</li></ul></div>
<div class="abs foot-col" style="left:550px;width:100px"><h4>Support</h4><ul><li>Partner</li><li>Blog</li><li>Let's Chat</li><li>Careers</li></ul></div>
<div class="abs foot-col" style="left:747px;width:180px"><h4>Contact Info</h4><ul><li>Quis nostrud exerc nostrud</li><li>123456- feugiat nulla</li></ul><p class="phone">123-456-7890</p></div>
<div class="abs foot-rule"></div>
<span class="abs legal" style="left:486px">© 2021solven</span>
<span class="abs legal" style="left:590px">Privacy Policy</span>
<span class="abs legal" style="left:678px">Quality</span>

</body>
</html>
```